Northgate Claims Advocates Business card

We need to get business card Design for our Company we are Public Adjusters in Chicago Illinois - i like to see good combination and elements from my Company Logo. as well To be an two side design
Updates

Target Market(s)

Home /Business owner Property Managers

Industry/Entity Type

Business

Contact Information for Business Card

to show the Element of our logo i will Like 3D

Font styles to use
Sans Serif

Requirements
Must have
• Logo and Element of the Logo in 3D
Nice to have
• Logo That we Provide 3D Same Colors or open for suggestions
Should not have
• unleare view -

```html
<!DOCTYPE html>
<html lang="en">
<head>
<meta charset="utf-8">
<title>Northgate Claims Advocates — Business Card</title>
<link href="https://fonts.googleapis.com/css2?family=Open+Sans:wght@400;600;700&display=swap" rel="stylesheet">
<style>
  :root {
    --backdrop: #e3e3e3;
    --card: #ffffff;
    --brand-blue: #1b27c4;
    --icon-blue: #1a2fb5;
    --accent-red: #d2452b;
    --ink: #4a4a4a;
    --muted: #5a5a5a;
  }
  * { box-sizing: border-box; margin: 0; padding: 0; }
  html, body {
    width: 1200px;
    height: 987px;
    overflow: hidden;
    background: var(--backdrop);
    font-family: "Open Sans", sans-serif;
  }
  .sheet { position: relative; width: 1200px; height: 987px; }
  .card {
    position: absolute;
    left: 293px;
    width: 615px;
    height: 351px;
    background: var(--card);
    overflow: hidden;
  }
  .card--front { top: 130px; }
  .card--back { top: 505px; }

  /* front */
  .brand-block {
    position: absolute;
    left: 30px;
    top: 0;
    width: 290px;
    height: 351px;
    display: flex;
    flex-direction: column;
    align-items: center;
    justify-content: center;
    gap: 18px;
    text-align: center;
  }
  .brand-mark {
    width: 64px;
    height: 64px;
    border-radius: 50%;
    background: var(--brand-blue);
    flex: none;
  }
  .brand-name {
    color: var(--brand-blue);
    font-weight: 700;
    font-size: 26px;
    line-height: 1.2;
  }
  .edge-tab {
    position: absolute;
    right: -24px;
    top: 103px;
    width: 48px;
    height: 48px;
    border-radius: 50%;
    background: var(--brand-blue);
  }
  .contact {
    position: absolute;
    right: 40px;
    top: 100px;
    text-align: right;
    color: var(--ink);
  }
  .contact__name {
    color: var(--brand-blue);
    font-weight: 600;
    font-size: 22px;
    line-height: 1.1;
    letter-spacing: 0.3px;
  }
  .contact__title {
    color: var(--accent-red);
    font-size: 17px;
    line-height: 1.3;
    margin-bottom: 10px;
  }
  .contact__address {
    font-size: 16px;
    line-height: 1.4;
    margin-bottom: 8px;
  }
  .contact__list { list-style: none; }
  .contact__item {
    display: flex;
    justify-content: flex-end;
    align-items: center;
    gap: 7px;
    font-size: 15.5px;
    line-height: 23.5px;
  }
  .contact__item svg { width: 15px; height: 15px; fill: var(--icon-blue); flex: none; }

  /* back */
  .back-brand {
    position: absolute;
    left: 0;
    right: 0;
    top: 150px;
    display: flex;
    justify-content: center;
    align-items: center;
    gap: 12px;
  }
  .back-brand .brand-mark { width: 40px; height: 40px; }
  .back-brand .brand-name { font-size: 24px; }
  .back-url {
    position: absolute;
    left: 0;
    right: 0;
    top: 285px;
    text-align: center;
    color: var(--muted);
    font-size: 16px;
    letter-spacing: 2.4px;
  }
</style>
</head>
<body>
<main class="sheet">
  <section class="card card--front">
    <div class="brand-block">
      <span class="brand-mark"></span>
      <p class="brand-name">Northgate Claims<br>Advocates</p>
    </div>
    <span class="edge-tab"></span>
    <div class="contact">
      <h1 class="contact__name">MARCUS HALE</h1>
      <p class="contact__title">CEO/Founder</p>
      <p class="contact__address">2140 Lakeview Court<br>Springfield, Illinois 60614</p>
      <ul class="contact__list">
        <li class="contact__item">312 555 0147
          <svg viewBox="0 0 24 24" aria-hidden="true"><path d="M6.6 10.8a15.1 15.1 0 0 0 6.6 6.6l2.2-2.2c.3-.3.7-.4 1-.2 1.1.4 2.3.6 3.6.6.6 0 1 .4 1 1V20c0 .6-.4 1-1 1A17 17 0 0 1 3 4c0-.6.4-1 1-1h3.5c.6 0 1 .4 1 1 0 1.3.2 2.5.6 3.6.1.3 0 .7-.2 1z"/></svg>
        </li>
        <li class="contact__item">312 555 0182
          <svg viewBox="0 0 24 24" aria-hidden="true"><path d="M7 1h10a2 2 0 0 1 2 2v18a2 2 0 0 1-2 2H7a2 2 0 0 1-2-2V3a2 2 0 0 1 2-2zm0 3v14h10V4zm5 15.5a1 1 0 1 0 0 2 1 1 0 0 0 0-2z"/></svg>
        </li>
        <li class="contact__item">312 555 0193
          <svg viewBox="0 0 24 24" aria-hidden="true"><path d="M6 2h10l2 2v5H6zM3 10h18a2 2 0 0 1 2 2v6h-4v4H5v-4H1v-6a2 2 0 0 1 2-2zm4 6v4h10v-4z"/></svg>
        </li>
        <li class="contact__item">hello@northgateclaims.com
          <svg viewBox="0 0 24 24" aria-hidden="true"><path d="M2 5h20v14H2zm2 2v.5l8 5 8-5V7zm0 3v7h16v-7l-8 5z"/></svg>
        </li>
        <li class="contact__item">www.northgateclaims.com
          <svg viewBox="0 0 24 24" aria-hidden="true"><path d="M12 2a10 10 0 1 0 0 20 10 10 0 0 0 0-20zm-1 17.9A8 8 0 0 1 4.2 10L9 14.8V16a2 2 0 0 0 2 2zm6.9-2.5A2 2 0 0 0 16 16h-1v-3a1 1 0 0 0-1-1H8v-2h2a1 1 0 0 0 1-1V7h2a2 2 0 0 0 2-2v-.4a8 8 0 0 1 2.9 12.8z"/></svg>
        </li>
      </ul>
    </div>
  </section>

  <section class="card card--back">
    <div class="back-brand">
      <span class="brand-mark"></span>
      <p class="brand-name">Northgate Claims Advocates</p>
    </div>
    <p class="back-url">www.NorthgateClaimsAdvocates.com</p>
  </section>
</main>
</body>
</html>
```